Agriculture farming Hemp and CBD

The logo is in works with your company now, should be ready in a few days. We have our Domain (kestrelbrookhollow.com) We would like to see incorporated seed to growth, but not necessary. we would like to nature colors and some black and green. we have our farm and will be growing and selling HEMP and CBD we are based in the state of Virginia. Would like to incorporate the words pause, play, rewind if possible but not necessary.

Target Market(s)

20 years old to elderly

Coding

Coded - Design and coding required

Number of Pages Required

3 page

Font styles to use
Serif

Requirements
Must have
• I'm not sure on the must haves, we are open to any ideas, we would definitely like to see Hemp and CBD included, may the life cycle of seed to plant. We must have a pop up asking if you are 20 years old before they can enter our site and to view or purchase our product. I want the design to be totally different than what i uploaded.
Nice to have
• Would like to see natural colors as well as black and green
Should not have
• I want

```html
<!DOCTYPE html>
<html lang="en">
<head>
<meta charset="utf-8">
<title>Kestrel Brook Hollow – Hemp &amp; CBD Farming</title>
<link href="https://fonts.googleapis.com/css2?family=Lato:wght@400;700;900&family=Merriweather:wght@900&display=swap" rel="stylesheet">
<style>
:root{
  --green:#0f8a2c;
  --green-dark:#0b6e22;
  --green-bright:#12e41c;
  --green-soft:#8fe08c;
  --green-text:#119b2b;
  --ink:#1b1b1b;
  --muted:#333;
  --white:#fff;
  --footer:#101010;
}
*{margin:0;padding:0;box-sizing:border-box}
html,body{width:1200px;height:3086px;overflow:hidden}
body{position:relative;font-family:'Lato',sans-serif;color:var(--ink);background:var(--white)}
.abs{position:absolute}
.photo{position:absolute}
.hero{position:absolute;left:0;top:0;width:1200px;height:583px;background:linear-gradient(110deg,#6b6a3f 0%,#4d6b2b 30%,#5b7a33 55%,#6f8a3a 80%,#596c2e 100%)}
.hero-shade{position:absolute;inset:0;background:linear-gradient(90deg,rgba(0,0,0,.05),rgba(0,0,0,.25))}
.logo{font-family:'Lato',sans-serif;font-weight:700;color:var(--white);font-size:28px;letter-spacing:.3px;white-space:nowrap}
.topmail{left:590px;top:20px;color:#fff;font-size:14px;font-weight:700;display:flex;align-items:center;gap:10px}
.icon-dot{width:30px;height:30px;border-radius:50%;background:var(--green-bright);display:flex;align-items:center;justify-content:center}
.follow{left:866px;top:20px;display:flex;align-items:center;gap:8px;color:#fff;font-size:12px;font-weight:700}
.soc{width:30px;height:30px;border-radius:50%;background:#fff;display:inline-block}
.nav{top:79px;color:#fff;font-size:16px;font-weight:700;white-space:nowrap}
.hero-t1{left:560px;top:254px;color:#fff;font-size:27px;font-weight:700}
.hero-t2{left:560px;top:292px;color:#fff;font-size:47px;font-weight:700;white-space:nowrap}
.hero-t3{left:560px;top:366px;color:#fff;font-size:30px;font-weight:700}
.dots{left:560px;top:515px;display:flex;gap:6px;align-items:center}
.dots i{display:block;width:9px;height:9px;border-radius:50%;background:#fff}
.dots b{display:block;width:42px;height:7px;border-radius:4px;background:#fff}
.h-welcome{left:137px;top:652px;width:470px;font-size:22px;font-weight:700;color:var(--ink);white-space:nowrap}
.sub-welcome{left:136px;top:694px;font-size:17px;font-weight:700;color:var(--green-text)}
.para{left:137px;top:732px;width:468px;font-size:14px;line-height:24px;text-align:justify;color:var(--muted)}
.btn{position:absolute;display:flex;align-items:center;justify-content:center;gap:8px;background:var(--green);color:#fff;font-weight:700;font-size:14px;border-radius:22px}
.welcome-frame{left:645px;top:685px;width:419px;height:313px;background:var(--green-soft)}
.services{position:absolute;left:0;top:1086px;width:1200px;height:533px;background:linear-gradient(180deg,#0f8a2c,#0d8329)}
.sec-title{position:absolute;width:1200px;text-align:center;font-size:33px;font-weight:700;color:#fff}
.card-label{position:absolute;height:87px;background:#fff;display:flex;align-items:center;justify-content:space-between;padding:0 18px;font-size:16px;font-weight:700;line-height:27px;color:var(--ink)}
.card-label.active{background:var(--green-bright);color:#fff}
.kicker{left:135px;top:1683px;font-size:14px;letter-spacing:1.5px;color:var(--green-text)}
.h-serif{left:135px;top:1706px;font-family:'Merriweather',serif;font-weight:900;font-size:29px;letter-spacing:1.5px;color:var(--green-text);white-space:nowrap}
.prod-para{left:471px;top:1680px;width:594px;font-size:14px;line-height:22px;color:var(--muted)}
.prod-img{position:absolute;top:1794px;height:186px;border:1px solid #cfcfcf}
.prod-name{position:absolute;top:1998px;font-size:19px;font-weight:700;text-align:center;width:212px}
.prod-price{position:absolute;top:2029px;font-size:19px;font-weight:700;text-align:center;width:212px;color:var(--green-text)}
.dark{position:absolute;left:0;top:2189px;width:1200px;height:557px;background:radial-gradient(ellipse at 30% 40%,#2c4a22,#17281a 60%,#0f1c10)}
.dark-title{position:absolute;top:2245px;font-size:28px;font-weight:700;color:#fff}
.blog-img{position:absolute;left:137px;width:129px;height:130px;border:2px solid #ddd}
.blog-cat{position:absolute;left:297px;font-size:16px;font-weight:700;color:#fff}
.blog-txt{position:absolute;left:297px;font-size:17px;line-height:24px;color:#fff}
.blog-date{position:absolute;left:297px;font-size:14px;color:#fff}
.blog-line{position:absolute;left:297px;width:239px;height:1px;background:rgba(255,255,255,.35)}
.field{position:absolute;left:683px;width:379px;background:#fff;font-size:14px;color:#555;padding:16px 19px}
.btn-pill{position:absolute;display:flex;align-items:center;justify-content:center;background:var(--green-bright);color:#fff;font-weight:700;font-size:15px;border-radius:22px;border:2px solid #0c6d1d}
.footer{position:absolute;left:0;top:2746px;width:1200px;height:340px;background:var(--footer)}
.f-head{position:absolute;top:2788px;font-size:15px;font-weight:700;color:var(--green-bright)}
.f-list{position:absolute;top:2824px;list-style:none;font-size:12.5px;line-height:24px;color:#fff}
.f-contact{position:absolute;left:874px;top:2824px;font-size:12.5px;line-height:20px;color:#fff}
.f-contact div{display:flex;gap:8px;align-items:flex-start;margin-bottom:4px}
.soc-g{width:28px;height:28px;border-radius:50%;border:2px solid #fff;background:var(--green);display:inline-block}
.copy{position:absolute;top:3048px;width:1200px;text-align:center;font-size:12px;font-weight:700;color:var(--green-bright)}
</style>
</head>
<body>

<section class="hero" role="img" aria-label="Hands holding a young hemp plant in a green field">
  <div class="hero-shade"></div>
</section>
<div class="abs topmail"><span class="icon-dot"><svg width="14" height="10" viewBox="0 0 14 10"><rect x="0.5" y="0.5" width="13" height="9" fill="#fff"/><path d="M1 1l6 5 6-5" stroke="#12e41c" stroke-width="1.4" fill="none"/></svg></span>info@kestrelbrookhollow.com</div>
<div class="abs follow">FOLLOW US: <span class="soc"></span><span class="soc"></span><span class="soc"></span></div>
<div class="abs logo" style="left:135px;top:62px">kestrelbrookhollow.com</div>
<div class="abs nav" style="left:505px">HOME</div>
<div class="abs nav" style="left:595px">ABOUT US</div>
<div class="abs nav" style="left:710px">OUR SERVICES</div>
<div class="abs nav" style="left:859px">PRODUCT</div>
<div class="abs nav" style="left:966px">CONTACT US</div>
<div class="abs hero-t1">WE ARE DOING</div>
<div class="abs hero-t2">AGRICULTURE FARMING</div>
<div class="abs hero-t3">HEMP AND CBD PRODUCTS</div>
<div class="abs dots"><i></i><i></i><b></b></div>

<h1 class="abs h-welcome">WELCOME TO KESTRELBROOKHOLLOW.COM</h1>
<p class="abs sub-welcome">We are doing agricultural farming of hemp products</p>
<p class="abs para">Lorem Ipsum is simply long established fact that a reader will be distracted by the readable content of a page when looking at its layout. The point of using Lorem Ipsum is that it has more-or-less normal distribution of letters, as opposed to using 'Content here, content here', making it look like readable English. Many desktop publishing packages and web page editors now use Lorem Ipsum as their default model text, and a search for 'lorem ipsum' will uncover many web sites still in their infancy. Various versions have evolved over the years, sometimes by accident, sometimes on purpose injected humour and the like.</p>
<div class="btn" style="left:137px;top:975px;width:136px;height:37px">More Info <svg width="16" height="8" viewBox="0 0 16 8"><path d="M0 4h14M10 0l4 4-4 4" stroke="#fff" stroke-width="1.6" fill="none"/></svg></div>
<div class="abs welcome-frame"></div>
<div class="photo" style="left:671px;top:654px;width:392px;height:316px;background:linear-gradient(135deg,#3f7a25,#6fa640 55%,#4c8a2d)" role="img" aria-label="CBD oil dropper with cannabidiol molecule diagram on green background"></div>

<section class="services" role="img" aria-label="Green background with faint hemp leaves"></section>
<h2 class="sec-title" style="top:1125px">OUR SERVICES</h2>
<div class="photo" style="left:139px;top:1201px;width:288px;height:274px;background:linear-gradient(160deg,#e8e2d6,#c9bfa8 60%,#a49a7c)" role="img" aria-label="Hemp buds in glass jars with tweezers"></div>
<div class="photo" style="left:456px;top:1201px;width:289px;height:274px;background:linear-gradient(160deg,#d9f0e6,#8fd39a 50%,#46a9c9)" role="img" aria-label="Hemp leaf in laboratory glassware"></div>
<div class="photo" style="left:775px;top:1201px;width:288px;height:274px;background:linear-gradient(160deg,#4e8a35,#2f6a24 50%,#5b9a3f)" role="img" aria-label="Hemp plants growing in a field"></div>
<div class="card-label" style="left:139px;top:1475px;width:288px"><span>SEED BREEDING AND<br>GENETIC DEVELOPMENT</span><svg width="24" height="10" viewBox="0 0 24 10"><path d="M0 5h22M17 1l5 4-5 4" stroke="#0f8a2c" stroke-width="2" fill="none"/></svg></div>
<div class="card-label active" style="left:456px;top:1475px;width:289px"><span>PRODUCT RESEARCH AND<br>DEVELOPMENT</span><svg width="24" height="10" viewBox="0 0 24 10"><path d="M0 5h22M17 1l5 4-5 4" stroke="#0f8a2c" stroke-width="2" fill="none"/></svg></div>
<div class="card-label" style="left:775px;top:1475px;width:288px"><span>PLANT CULTIVATION AND<br>FARMING</span><svg width="24" height="10" viewBox="0 0 24 10"><path d="M0 5h22M17 1l5 4-5 4" stroke="#0f8a2c" stroke-width="2" fill="none"/></svg></div>

<div class="abs kicker">WE ARE SELLING</div>
<h2 class="abs h-serif">HEMP PRODUCTS</h2>
<p class="abs prod-para">Succeeding in the life sciences industry is as much about strategy and execution as it is about research and development new initiative aimed at supporting emerging companies within the life sciences sector</p>
<div class="prod-img" style="left:135px;width:213px;background:radial-gradient(circle,#5d6e32 0 30%,#e6e6e6 45%)" role="img" aria-label="Dried hemp bud"></div>
<div class="prod-img" style="left:374px;width:211px;background:linear-gradient(160deg,#d6d2c8,#b59a3a 50%,#8a6a3a)" role="img" aria-label="Hemp seed oil bottle with seeds"></div>
<div class="prod-img" style="left:611px;width:213px;background:linear-gradient(160deg,#dfe7dc,#b07a1e 50%,#2c3a2a)" role="img" aria-label="CBD tincture bottle with leaves"></div>
<div class="prod-img" style="left:849px;width:213px;background:linear-gradient(160deg,#e6e9ec,#f7f7f7 50%,#c8cdd2)" role="img" aria-label="Pre-rolled hemp cones"></div>
<div class="prod-name" style="left:135px">PRODUCT 1</div><div class="prod-price" style="left:135px">$112.50</div>
<div class="prod-name" style="left:370px">PRODUCT 2</div><div class="prod-price" style="left:370px">$125.50</div>
<div class="prod-name" style="left:611px">PRODUCT 3</div><div class="prod-price" style="left:611px">$155.50</div>
<div class="prod-name" style="left:851px">PRODUCT 4</div><div class="prod-price" style="left:851px">$165.50</div>
<div class="btn" style="left:522px;top:2093px;width:136px;height:39px">View All <svg width="16" height="8" viewBox="0 0 16 8"><path d="M0 4h14M10 0l4 4-4 4" stroke="#fff" stroke-width="1.6" fill="none"/></svg></div>

<section class="dark" role="img" aria-label="Dark background of hemp leaves"></section>
<h2 class="dark-title" style="left:134px">LATEST BLOG</h2>
<div class="blog-img" style="top:2323px;background:linear-gradient(135deg,#f1f1f1,#d9d5c9 60%,#7d8a4a)" role="img" aria-label="Hand holding a rolled hemp product"></div>
<div class="blog-cat" style="top:2320px">CONSULTANT PROJECT</div>
<div class="blog-txt" style="top:2351px">Workplace Transition -<br>Critical elements to consider</div>
<div class="blog-line" style="top:2413px"></div>
<div class="blog-date" style="top:2437px">12 August 2020</div>
<div class="blog-img" style="top:2484px;background:linear-gradient(160deg,#3c6a2c,#8aa06a 50%,#e8ecef)" role="img" aria-label="Researcher standing in a hemp field"></div>
<div class="blog-cat" style="top:2485px;left:299px">NEW DEVELOPMENT</div>
<div class="blog-txt" style="top:2516px;left:299px">Workplace Transition -<br>Critical elements to consider</div>
<div class="blog-line" style="top:2580px;left:299px"></div>
<div class="blog-date" style="top:2593px;left:299px">12 August 2020</div>
<div class="btn-pill" style="left:138px;top:2652px;width:123px;height:40px">VIEW ALL</div>

<h2 class="dark-title" style="left:683px">GET IN TOUCH</h2>
<div class="field" style="top:2314px;height:50px">Enter Full Name</div>
<div class="field" style="top:2375px;height:49px">Enter Email Address</div>
<div class="field" style="top:2435px;height:50px">Enter Phone Number</div>
<div class="field" style="top:2496px;height:138px">Type Message</div>
<div class="btn-pill" style="left:683px;top:2652px;width:115px;height:40px">SUBMIT</div>

<footer class="footer"></footer>
<div class="abs logo" style="left:138px;top:2790px;font-size:24px">kestrelbrookhollow.com</div>
<div class="abs" style="left:138px;top:2848px;display:flex;gap:12px"><span class="soc-g"></span><span class="soc-g"></span><span class="soc-g"></span></div>
<div class="f-head" style="left:499px">Main Links</div>
<ul class="f-list" style="left:499px"><li>Home</li><li>About Us</li><li>Services</li><li>Products</li><li>Blog</li><li>Contact Us</li></ul>
<div class="f-head" style="left:673px">Info Links</div>
<ul class="f-list" style="left:673px"><li>Latest Blog</li><li>Terms and Conditions</li><li>Privacy Policy</li></ul>
<div class="f-head" style="left:874px">Contact Us</div>
<div class="f-contact">
  <div><svg width="10" height="14" viewBox="0 0 10 14"><path d="M5 0a5 5 0 0 1 5 5c0 4-5 9-5 9S0 9 0 5a5 5 0 0 1 5-5z" fill="#12e41c"/><circle cx="5" cy="5" r="2" fill="#101010"/></svg><span>4th Floor, Suite C,<br>Virginia</span></div>
  <div><svg width="12" height="12" viewBox="0 0 12 12"><path d="M2 0l3 3-1.5 1.5a7 7 0 0 0 4 4L9 7l3 3-2 2C5 12 0 7 0 2z" fill="#12e41c"/></svg><span>+ 1 540 555 0142<br>+1 540 555 0178</span></div>
  <div><svg width="14" height="10" viewBox="0 0 14 10"><rect width="14" height="10" fill="#12e41c"/><path d="M1 1l6 5 6-5" stroke="#101010" stroke-width="1.3" fill="none"/></svg><span>info@kestrelbrookhollow.com</span></div>
</div>
<div class="copy">kestrelbrookhollow.com © 2020. All Rights Reserved.</div>

</body>
</html>
```